Corvane Holdings , new business card design

investment firm with corporate clients . need double sided business card , vertical and horizontal options ,logo must be clear. prefer pantone colors only and sharp design. website also www.corvane.ae

Khalid Bin Tarrafi
Managing Director
Tel. +971 4 387 2940
Mobile +971 50 518 2403
khalid@corvane.ae
Q-Span Plaza, officw 18-B07, Warqa Gardens, Dubai

Contact Information for Business Card

Khalid Bin Tarrafi
Managing Director

Font styles to use
Serif

Colors

Designer to choose colors to be used in the design.

```html
<!DOCTYPE html>
<html lang="en">
<head>
<meta charset="utf-8">
<title>Corvane Holdings — Business Card</title>
<link rel="stylesheet" href="https://fonts.googleapis.com/css2?family=Lato:wght@300;400;700&display=swap">
<style>
  :root {
    --stage: #e6e4e0;
    --card-black: #0b0b0e;
    --card-white: #f8f8f6;
    --ink: #262626;
    --ink-soft: #3a3a3a;
    --rule: #5a5a5a;
    --accent-blue: #44698f;
    --on-black: #ffffff;
  }
  * { box-sizing: border-box; margin: 0; padding: 0; }
  html, body {
    width: 1200px; height: 1200px; overflow: hidden;
    background: var(--stage);
    font-family: "Lato", sans-serif;
  }
  .stage {
    width: 1200px; height: 1200px;
    display: flex; flex-direction: column;
    align-items: center; justify-content: center; gap: 60px;
  }
  .card {
    position: relative;
    width: 840px; height: 480px;
    border-radius: 4px;
    overflow: hidden;
  }
  /* Front */
  .card-front {
    background: var(--card-black);
    display: flex; align-items: center; justify-content: center;
  }
  .front-wordmark {
    color: var(--on-black);
    font-weight: 300;
    font-size: 50px;
    letter-spacing: 0.22em;
    text-transform: uppercase;
    padding-left: 0.22em;
  }
  /* Back */
  .card-back {
    background: var(--card-white);
    color: var(--ink);
    box-shadow: 0 0 0 1px #d6d4cf;
  }
  .brand-column {
    position: absolute; left: 0; top: 0;
    width: 270px; height: 480px;
    display: flex; align-items: center; justify-content: center; gap: 26px;
  }
  .brand-column .vertical {
    writing-mode: vertical-rl;
    transform: rotate(180deg);
    white-space: nowrap;
  }
  .brand-wordmark {
    font-weight: 300;
    font-size: 30px;
    letter-spacing: 0.12em;
    text-transform: uppercase;
    color: var(--ink);
    display: flex; align-items: center; gap: 14px;
  }
  .brand-mark {
    width: 12px; height: 12px;
    background: var(--accent-blue);
    flex: none;
  }
  .website {
    font-weight: 400;
    font-size: 21px;
    color: var(--ink);
  }
  .column-rule {
    position: absolute; left: 270px; top: 36px;
    width: 1.5px; height: 408px;
    background: var(--rule);
  }
  .details {
    position: absolute; left: 270px; top: 0; right: 0; height: 480px;
  }
  .identity { position: absolute; left: 34px; top: 52px; }
  .person-name { font-weight: 400; font-size: 38px; color: var(--ink); }
  .person-title { font-weight: 400; font-size: 22px; color: var(--ink-soft); margin-top: 4px; }
  .row-rule {
    position: absolute; left: 0; right: 36px; height: 1.5px; background: var(--rule);
  }
  .row-rule.first { top: 150px; }
  .row-rule.second { top: 312px; }
  .contacts {
    position: absolute; left: 34px; top: 172px;
    display: grid; grid-template-columns: auto auto auto; column-gap: 12px; row-gap: 4px;
    font-size: 28px; font-weight: 400; color: var(--ink);
  }
  .address {
    position: absolute; left: 34px; top: 334px;
    font-size: 21px; line-height: 1.4; color: var(--ink-soft);
  }
</style>
</head>
<body>
  <main class="stage">
    <section class="card card-front" aria-label="Card front">
      <div class="front-wordmark">Corvane Holdings</div>
    </section>

    <section class="card card-back" aria-label="Card back">
      <div class="brand-column">
        <div class="brand-wordmark vertical"><span class="brand-mark"></span>Corvane Holdings</div>
        <div class="website vertical">www.corvane.ae</div>
      </div>
      <div class="column-rule"></div>
      <div class="details">
        <div class="identity">
          <h1 class="person-name">Khalid Bin Tarrafi</h1>
          <p class="person-title">Managing Director</p>
        </div>
        <div class="row-rule first"></div>
        <div class="contacts">
          <span>Tel</span><span>:</span><span>+971 4 387 2940</span>
          <span>Mobile</span><span>:</span><span>+971 50 518 2403</span>
          <span>Email</span><span>:</span><span>khalid@corvane.ae</span>
        </div>
        <div class="row-rule second"></div>
        <p class="address">Q-Span Plaza, officw 18-B07,<br>Warqa Gardens, Dubai</p>
      </div>
    </section>
  </main>
</body>
</html>
```